Marwick Law Letterhead

We need a new letterhead design for a Law Firm. The address for the law firm is 1475 Calloway Street, Suite 210, Houston, Texas 77041. Phone Number: 832-361-9027; Fax Number: 832-614-7359. The logo is uploaded to the project.

```html
<!DOCTYPE html>
<html lang="en">
<head>
<meta charset="utf-8">
<title>Marwick Law Letterhead</title>
<link href="https://fonts.googleapis.com/css2?family=Figtree:wght@400;500&display=swap" rel="stylesheet">
<style>
  :root {
    --navy: #1b2d5e;
    --red: #d7161f;
    --red-mid: #a80d17;
    --red-deep: #7a0510;
    --ink: #2f2f33;
    --backdrop: #e8e8e8;
    --paper: #ffffff;
  }
  * { margin: 0; padding: 0; box-sizing: border-box; }
  html, body {
    width: 1154px;
    height: 1200px;
    overflow: hidden;
    background: var(--backdrop);
    font-family: "Figtree", Arial, sans-serif;
    color: var(--ink);
  }
  .letterhead {
    position: absolute;
    left: 162px;
    top: 20px;
    width: 830px;
    height: 1160px;
    background: var(--paper);
    overflow: hidden;
  }
  .brand {
    position: absolute;
    left: 33px;
    top: 68px;
    display: flex;
    align-items: center;
    gap: 14px;
  }
  .brand-mark {
    width: 52px;
    height: 52px;
    background: var(--navy);
  }
  .brand-name {
    font-size: 38px;
    font-weight: 500;
    color: var(--navy);
    letter-spacing: 0.5px;
  }
  .contact {
    position: absolute;
    left: 609px;
    top: 56px;
    height: 97px;
    border-left: 1.5px solid var(--red);
    padding-left: 20px;
    font-size: 14.5px;
    line-height: 18px;
    font-style: normal;
    color: #1a1a1a;
  }
  .contact-lines { margin-top: 12px; }
  .contact-line {
    display: flex;
    align-items: center;
    gap: 9px;
    height: 20.5px;
  }
  .contact-line svg { width: 13px; height: 13px; flex: none; }
  .recipient {
    position: absolute;
    left: 31px;
    top: 246px;
    font-size: 15px;
    line-height: 20.6px;
  }
  .body-copy {
    position: absolute;
    left: 33px;
    top: 330px;
    width: 768px;
    font-size: 15.4px;
    line-height: 20.6px;
    text-align: justify;
  }
  .body-copy p + p { margin-top: 20.6px; }
  .closing {
    position: absolute;
    left: 30px;
    top: 912px;
    font-size: 17px;
  }
  .signature {
    position: absolute;
    left: 29px;
    top: 944px;
    width: 92px;
    height: 26px;
    border-radius: 3px;
    background: linear-gradient(90deg, #d9dbe2, #eceef2);
  }
  .footer-band {
    position: absolute;
    left: 0;
    bottom: 0;
    width: 830px;
    height: 110px;
    background: linear-gradient(90deg, var(--red), var(--red-mid) 55%, var(--red-deep));
  }
</style>
</head>
<body>
  <main class="letterhead">
    <header>
      <div class="brand">
        <div class="brand-mark"></div>
        <div class="brand-name">Marwick Law</div>
      </div>
      <address class="contact">
        <div class="contact-address">1475 Calloway Street,<br>Suite 210, Houston,<br>Texas 77041</div>
        <div class="contact-lines">
          <div class="contact-line">
            <svg viewBox="0 0 16 16" aria-label="Phone"><path fill="#d7161f" d="M3.6 1.2l2.3 2.5-1.4 1.7c.9 2 2.3 3.4 4.3 4.3l1.7-1.4 2.5 2.3-1.2 2.3C7 12.6 3.4 9 1.2 4.1z"/><path fill="none" stroke="#d7161f" stroke-width="1.2" d="M9.5 1.5a5 5 0 0 1 5 5M9.5 4a2.5 2.5 0 0 1 2.5 2.5"/></svg>
            <span>832-361-9027</span>
          </div>
          <div class="contact-line">
            <svg viewBox="0 0 16 16" aria-label="Fax"><rect x="4" y="1" width="8" height="5" fill="#d7161f"/><rect x="1" y="5" width="14" height="7" rx="1.5" fill="#d7161f"/><rect x="4" y="9" width="8" height="6" fill="#fff" stroke="#d7161f" stroke-width="1.2"/></svg>
            <span>832-614-7359</span>
          </div>
        </div>
      </address>
    </header>

    <section class="recipient">
      <div>Mr/s</div>
      <div>First Name and Last Name</div>
      <div>Company Name</div>
      <div>Address</div>
    </section>

    <section class="body-copy">
      <p>Lorem ipsum dolor sit amet,consectetur adipiscing sed do eiusmod tempor incididunt laboreet dolore magna aliqua.Ut enim ad minim.veniam, quis nostrud exercitation ullamco laboris nisi ut aliquip exea commodo consequat.Lorem ipsum dolor sit amet,consectetur adipiscing sed do eiusmod tempor incididunt.labore et dolore magna aliqua. Ut enim</p>
      <p>Lorem ipsum dolor sit amet, consectetur adipiscing sed do eiusmod tempor incididunt labore et dolore magna aliqua. Ut enim ad minim veniam, quis nostrud exercitation ullamco laboris nisi ut aliquip exea commodo consequat.Duis aute irure dolor in reprehenderit in voluptate velit esse cillum irure dolor in reprehenderit in voluptate velit esse irure</p>
      <p>Lorem ipsum dolor sit amet, consectetur adipiscing sed do eiusmod tempor incididunt labore et dolore magna aliqua. consequat. Duis aute irure dolor in.reprehenderit in voluptate velit esse cillum dolore eu fugiat nulla pariatur. Excepteur sint occaecat cupidatat non proident, sunt in culpa qui officia deserunt mollit,</p>
      <p>Lorem ipsum dolor sit amet, consectetur adipiscing sed do eiusmod tempor incididunt labore et dolore magna aliqua. Ut enim Lorem ipsum dolor sit amet, consectetur adipiscing sed do eiusmod tempor incididunt labore et dolore magna aliqua. Ut enim Lorem ipsum aliqua.ipsum</p>
      <p>Lorem ipsum dolor sit amet, consectetur adipiscing sed do eiusmod tempor incididunt labore et dolore magna aliqua. Ut enim ad minim veniam, quis nostrud exercitation ullamco laboris nisi ut aliquip exea commodo consequat.Duis aute irure dolor in reprehenderit in voluptate velit esse cillum irure dolor in reprehenderit in voluptate velit esse irure</p>
      <p>Lorem ipsum dolor sit amet, consectetur adipiscing sed do eiusmod tempor incididunt labore et dolore magna aliqua. Ut enim ad minim veniam, quis nostrud exercitation ullamco laboris nisi ut aliquip exea commodo consequat.Duis aute irure dolor in reprehenderit in voluptate velit esse cillum irure dolor in reprehenderit in voluptate velit esse irure</p>
    </section>

    <div class="closing">Regards</div>
    <div class="signature" role="img" aria-label="Handwritten signature of the sender"></div>

    <div class="footer-band" role="img" aria-label="Decorative navy and red footer artwork"></div>
  </main>
</body>
</html>
```